2022 Landscaping Services

Please use the prior year design as an example. Similar style but DO NOT COPY IT EXACTLY- you can use different photos from our website if you like. Same text for year 2022.
Design should clearly depict the differences between the 3 products so people can buy one of them. Be creative!

size 8.5" x 11"

Must provide source file in photoshop if you are winner

Requirements
Must have
• Same text as original flier but with year 2022

```html
<!DOCTYPE html>
<html lang="en">
<head>
<meta charset="utf-8">
<title>Maplewood Cemetery – 2022 Gravesite Landscaping Packages</title>
<link href="https://fonts.googleapis.com/css2?family=Bebas+Neue&family=Roboto:wght@400;700;900&family=Teko:wght@500;600&display=swap" rel="stylesheet">
<style>
:root{
  --red:#8c1c1c;
  --red-dark:#5e1010;
  --maroon:#7a1f2b;
  --ink:#1a1a1a;
  --stripe:#ededed;
  --white:#ffffff;
  --title-grey:#e3e3e3;
  --page:#e4e4e4;
}
*{margin:0;padding:0;box-sizing:border-box}
html,body{width:779px;height:1200px;overflow:hidden;background:var(--page);font-family:"Roboto",sans-serif}
.flyer{position:absolute;left:0;top:96px;width:779px;height:1008px;overflow:hidden;background:var(--red)}
.flyer-bg{position:absolute;inset:0}
.brand{position:absolute;left:70px;top:140px;width:190px;text-align:center;color:var(--red);font-family:"Roboto",sans-serif;font-weight:700;font-size:30px;line-height:1.05;letter-spacing:.5px}
.title{position:absolute;left:51px;top:252px;border-left:4px solid var(--white);padding-left:20px}
.title-year{font-family:"Bebas Neue",sans-serif;color:var(--white);font-size:62px;line-height:54px;letter-spacing:1px}
.title-sub{font-family:"Bebas Neue",sans-serif;color:var(--title-grey);font-size:50px;line-height:46px;letter-spacing:1px}
.card{position:absolute;left:49px;top:369px;width:677px;height:574px;background:var(--white);border-radius:14px}
.packages{position:absolute;left:21px;top:18px;display:grid;grid-template-columns:166px 152px 153px 164px;grid-template-rows:88px 75px repeat(6,45.5px) 100px}
.cell{display:flex;align-items:center;justify-content:center;border-right:1px solid #d6d6d6}
.cell:nth-child(4n){border-right:none}
.row-alt{background:var(--stripe)}
.head-services{background:var(--maroon);color:var(--white);font-weight:700;font-size:22px;line-height:26px;justify-content:flex-start;padding:0 18px;border-radius:12px 0 0 0}
.head-pkg{color:var(--red);font-weight:700;font-size:15.5px;line-height:20px;align-items:flex-start;justify-content:flex-start;padding:14px 16px 0}
.label{justify-content:flex-start;padding:0 18px;font-weight:700;font-size:11.5px;line-height:14px;color:var(--ink)}
.label.top{align-items:flex-start;padding-top:16px}
.freq{font-size:8.6px;line-height:11.5px;color:#444;align-items:flex-start;justify-content:flex-start;padding:14px 14px 0 16px}
.valid{background:var(--maroon);color:var(--white);font-weight:700;font-size:18px;line-height:30px;justify-content:flex-start;padding:0 18px;border-radius:0 0 0 12px}
.price{flex-direction:column;align-items:flex-start;justify-content:flex-start;padding:12px 14px 0 18px}
.price-big{color:var(--red);font-weight:900;font-size:30px;line-height:32px}
.price-note{font-size:8.6px;line-height:11.5px;color:#333;margin-top:8px}
.terms{display:flex;gap:8px}
.term b{display:block;color:var(--red);font-size:12.5px;line-height:15px}
.term span{display:block;background:var(--red);color:var(--white);font-size:7.5px;font-weight:700;padding:1px 4px;text-align:center}
.popular-frame{position:absolute;left:490px;top:16px;width:168px;height:540px;border:2.5px solid var(--maroon);border-radius:0 12px 12px 0;pointer-events:none}
.popular-tag{position:absolute;left:516px;top:6px;width:115px;height:20px;background:var(--maroon);color:var(--white);font-style:italic;font-weight:700;font-size:12px;line-height:20px;text-align:center;border-radius:3px}
.icon{width:22px;height:22px}
.footer{position:absolute;left:48px;top:956px;display:flex;align-items:center;font-family:"Teko",sans-serif;font-weight:500;color:var(--white);font-size:22px;line-height:24px}
.footer-item{display:flex;align-items:center;gap:8px;padding:0 10px;border-left:1px solid rgba(255,255,255,.5)}
.footer-item:first-child{border-left:none;padding-left:0}
.footer-item.web{font-size:19px}
.dot{width:16px;height:16px;border-radius:50%;background:var(--white);display:flex;align-items:center;justify-content:center}
</style>
</head>
<body>
<svg width="0" height="0" style="position:absolute">
  <symbol id="tick" viewBox="0 0 24 24"><polyline points="3,12 9,18 21,6" fill="none" stroke="#8c1c1c" stroke-width="2.6" stroke-linecap="round" stroke-linejoin="round"/></symbol>
  <symbol id="none" viewBox="0 0 24 24"><circle cx="12" cy="12" r="8.5" fill="none" stroke="#8c1c1c" stroke-width="2"/><line x1="6" y1="18" x2="18" y2="6" stroke="#8c1c1c" stroke-width="2"/></symbol>
</svg>

<main class="flyer">
  <svg class="flyer-bg" width="779" height="1008" viewBox="0 0 779 1008">
    <defs>
      <linearGradient id="redGrad" x1="0" y1="0" x2="0.3" y2="1">
        <stop offset="0" stop-color="#8e1d1d"/><stop offset="1" stop-color="#6d1414"/>
      </linearGradient>
      <linearGradient id="parkGrad" x1="0" y1="0" x2="0" y2="1">
        <stop offset="0" stop-color="#c9cfd2"/><stop offset=".45" stop-color="#8f9aa0"/><stop offset=".7" stop-color="#5f8a3a"/><stop offset="1" stop-color="#4d7a2c"/>
      </linearGradient>
      <radialGradient id="deerGrad" cx=".5" cy=".45" r=".6">
        <stop offset="0" stop-color="#8aa867"/><stop offset="1" stop-color="#3f6a2a"/>
      </radialGradient>
    </defs>
    <rect width="779" height="1008" fill="url(#redGrad)"/>
    <path d="M0 700 Q200 640 420 760 Q600 860 779 820 V1008 H0Z" fill="#6a1212" opacity=".55"/>
    <path d="M0 560 Q40 590 60 620 L0 660Z" fill="#ffffff"/>
    <path d="M0 600 Q50 640 70 690 L0 720Z" fill="#1a1a1a"/>
    <path d="M0 0 H779 V150 Q520 200 300 205 Q120 208 0 185Z" fill="#ffffff"/>
    <path d="M0 185 Q130 208 300 205 Q420 202 500 190 Q420 225 300 230 Q140 236 0 218Z" fill="#141414"/>
    <path d="M440 0 H779 V331 Q690 338 610 298 Q510 245 470 150 Q445 80 440 0Z" fill="#ffffff"/>
    <path role="img" aria-label="Photo of cemetery grounds with headstones, a flowering shrub and green lawn" d="M450 0 H779 V322 Q690 328 615 290 Q520 240 480 150 Q456 80 450 0Z" fill="url(#parkGrad)"/>
    <circle cx="394" cy="126" r="102" fill="#ffffff"/>
    <circle role="img" aria-label="Photo of a deer standing on the cemetery lawn" cx="394" cy="126" r="96" fill="url(#deerGrad)"/>
  </svg>

  <div class="brand">Maplewood<br>Cemetery</div>

  <div class="title">
    <div class="title-year">2022 Gravesite</div>
    <div class="title-sub">Landscaping Packages</div>
  </div>

  <section class="card">
    <div class="packages">
      <div class="cell head-services">SERVICES<br>OFFERED</div>
      <div class="cell head-pkg">SEASONAL<br>CARE<br>ENDOWMENT</div>
      <div class="cell head-pkg">BASIC CARE<br>ENDOWMENT</div>
      <div class="cell head-pkg">PERPETUAL<br>CARE<br>ENDOWMENT</div>

      <div class="cell label top row-alt">WEEDING &amp; TRIMMING<br>ON YOUR GRAVESITE</div>
      <div class="cell freq row-alt">Approximately every 7 weeks during the growing season: Mid-April through Mid-October</div>
      <div class="cell freq row-alt">2 times per year:<br>Mid-May &amp;Mid-September</div>
      <div class="cell freq row-alt">Approximately every 7 weeks during the growing season: Mid-April through Mid-October</div>

      <div class="cell label">PAYMENT ENSURED<br>FOREVER GRAVE CARE</div>
      <div class="cell"><svg class="icon"><use href="#none"/></svg></div>
      <div class="cell"><svg class="icon"><use href="#tick"/></svg></div>
      <div class="cell"><svg class="icon"><use href="#tick"/></svg></div>

      <div class="cell label row-alt">MONUMENT LEVELING</div>
      <div class="cell row-alt"><svg class="icon"><use href="#none"/></svg></div>
      <div class="cell row-alt"><svg class="icon"><use href="#tick"/></svg></div>
      <div class="cell row-alt"><svg class="icon"><use href="#tick"/></svg></div>

      <div class="cell label">MONUMENT CLEANING</div>
      <div class="cell"><svg class="icon"><use href="#none"/></svg></div>
      <div class="cell"><svg class="icon"><use href="#none"/></svg></div>
      <div class="cell"><svg class="icon"><use href="#tick"/></svg></div>

      <div class="cell label row-alt">FULL BED OF BOXWOOD<br>SHRUBS</div>
      <div class="cell row-alt"><svg class="icon"><use href="#none"/></svg></div>
      <div class="cell row-alt"><svg class="icon"><use href="#none"/></svg></div>
      <div class="cell row-alt"><svg class="icon"><use href="#tick"/></svg></div>

      <div class="cell label">REPLACEMENT<br>OF SHRUBS</div>
      <div class="cell"><svg class="icon"><use href="#none"/></svg></div>
      <div class="cell"><svg class="icon"><use href="#none"/></svg></div>
      <div class="cell"><svg class="icon"><use href="#tick"/></svg></div>

      <div class="cell label row-alt">TRUST CERTIFICATE</div>
      <div class="cell row-alt"><svg class="icon"><use href="#none"/></svg></div>
      <div class="cell row-alt"><svg class="icon"><use href="#none"/></svg></div>
      <div class="cell row-alt"><svg class="icon"><use href="#tick"/></svg></div>

      <div class="cell valid">Valid through<br>10/31/22</div>
      <div class="cell price">
        <div class="terms">
          <div class="term"><b>$357</b><span>3 Years</span></div>
          <div class="term"><b>$238</b><span>2 Years</span></div>
          <div class="term"><b>$119</b><span>1 Year</span></div>
        </div>
        <div class="price-note">Multi-year payment locks Call for single payment in current rates discounts.</div>
      </div>
      <div class="cell price">
        <div class="price-big">$255</div>
        <div class="price-note">12 Monthly payments.<br>Call for single payment discounts.</div>
      </div>
      <div class="cell price">
        <div class="price-big">$313</div>
        <div class="price-note">12 Monthly payments.<br>Call for single payment discounts.</div>
      </div>
    </div>
    <div class="popular-frame"></div>
    <div class="popular-tag">Most Popular</div>
  </section>

  <footer class="footer">
    <div class="footer-item"><span class="dot"><svg width="10" height="10" viewBox="0 0 24 24"><path d="M6 2l4 5-2 3c1.5 3 3 4.5 6 6l3-2 5 4-3 4C10 21 3 14 2 5z" fill="#8c1c1c"/></svg></span>(555) 210-4800</div>
    <div class="footer-item"><span class="dot"><svg width="10" height="10" viewBox="0 0 24 24"><path d="M12 2a7 7 0 0 0-7 7c0 5 7 13 7 13s7-8 7-13a7 7 0 0 0-7-7zm0 9.5a2.5 2.5 0 1 1 0-5 2.5 2.5 0 0 1 0 5z" fill="#8c1c1c"/></svg></span>48 ELM AVE. FAIRVIEW NJ 07000</div>
    <div class="footer-item web"><span class="dot"><svg width="10" height="10" viewBox="0 0 24 24"><circle cx="12" cy="12" r="9" fill="none" stroke="#8c1c1c" stroke-width="2.4"/><path d="M3 12h18M12 3c3 3 3 15 0 18M12 3c-3 3-3 15 0 18" fill="none" stroke="#8c1c1c" stroke-width="2"/></svg></span>MAPLEWOODCEMETERY.ORG</div>
  </footer>
</main>
</body>
</html>
```